Commercial Real Estate for Lease Listing Flyer

I am looking to put together a flyer for our available office space in our building. It needs to look professional and it will be standard sized 8.5 x 11 and double sided. Full color as well. This flyer will need to be able to be put in a PDF and a picture file that can be embedded in an email. I have included pictures, logo, and a Word document with the information you should need. Also, I included a bunch of SAMPLE leasing flyers that you can get ideas from. The floor plan is also included in here. I want it specifically noted that the top suite is Suite 100 and the bottom suite is 120. And list their size as well. I will be reviewing all designs very quickly, so be sure to check the comments.

• Please refer to these links for additional photos:
• "Twilight 1.jpg" at: https://files.plinthdocs.net/a/preview/3f7d1a92-b4e0-4c1a-8e5f-71c0d2ab9e34
• Twilight 2_straightened.jpg" at: https://files.plinthdocs.net/a/preview/a15c8e03-7d2b-4f9e-b6a1-0c93e4f72d58
• "Twilight 3.jpg" at: https://files.plinthdocs.net/a/preview/6e2b9f71-c3a4-4d08-9e7b-5f1a8c03d6e2
• "Twilight 4.jpg" at: https://files.plinthdocs.net/a/preview/c84a0d6e-1f3b-4e57-a2c9-9b7e05f4d813
• "Twilight 5.jpg" at: https://files.plinthdocs.net/a/preview/7b0f5c28-e6d1-4a93-8f4e-d25a1b6c07f9
• "Twilight 6.jpg" at: https://files.plinthdocs.net/a/preview/e3c6a417-5b92-4f0d-bc8e-4a1f97d2e065
• "Twilight 7.jpg" at: https://files.plinthdocs.net/a/preview/5a9d2e80-c7f4-4b16-93a0-e8b6f1c4d27a
• "Twilight 8.jpg" at: https://files.plinthdocs.net/a/preview/b2e7f069-84c3-4d5a-a71e-3c0d9b58f6e4
• "Twilight 9.jpg" at: https://files.plinthdocs.net/a/preview/4d8c1b3f-a0e5-4f72-8b69-f17e2c05a9d3
• "Twilight 10.jpg" at: https://files.plinthdocs.net/a/preview/f09a6c52-3e18-4b7d-9c24-6b5d80e1f3a7
• "Twilight 11.jpg" at: https://files.plinthdocs.net/a/preview/8e4f2d06-b9c7-4a31-85e0-d7a3c16f4b92

```html
<!DOCTYPE html>
<html lang="en">
<head>
<meta charset="utf-8">
<title>Hale Road Centre – Leasing Flyer</title>
<link rel="stylesheet" href="https://fonts.googleapis.com/css2?family=Montserrat:wght@300;400;500;600;700&family=Oswald:wght@600&display=swap">
<style>
  :root {
    --orange: #d98f2b;
    --orange-band: rgba(217, 143, 43, 0.88);
    --grey-bar: #7a7a7a;
    --ink: #5a5a5a;
    --ink-dark: #3f3f3f;
    --navy: #1f3f8a;
    --backdrop: #cfcfcf;
    --white: #ffffff;
  }
  * { box-sizing: border-box; margin: 0; padding: 0; }
  html, body { width: 1200px; height: 792px; overflow: hidden; }
  body {
    background: var(--backdrop);
    font-family: "Montserrat", sans-serif;
    color: var(--ink);
    position: relative;
  }
  .page {
    position: absolute;
    top: 77px;
    width: 498px;
    height: 643px;
    background: var(--white);
    overflow: hidden;
  }
  .page--front { left: 60px; }
  .page--back { left: 638px; }
  .block { position: absolute; background: var(--orange); }
  .photo { position: absolute; }
  .photo--office { background: linear-gradient(160deg, #b68a52 0%, #8a6a44 45%, #3a2c22 100%); }
  .photo--window { background: linear-gradient(120deg, #7e6248 0%, #c4a57a 55%, #e7d9bc 100%); }
  .photo--room { background: linear-gradient(180deg, #a98b62 0%, #87704f 60%, #3b2e25 100%); }
  .photo--framed { border: 4px solid var(--white); outline: 1px solid #b5b5b5; }

  /* Front */
  .hero { left: 23px; top: 23px; width: 451px; height: 299px; }
  .brand {
    position: absolute; left: 54px; top: 23px; width: 163px; height: 79px;
    background: rgba(255,255,255,0.94);
    display: flex; flex-direction: column; align-items: center; justify-content: center;
    color: var(--navy); font-weight: 500; line-height: 1;
  }
  .brand__name { font-size: 27px; letter-spacing: 3px; }
  .brand__sub { font-size: 12px; letter-spacing: 3.6px; margin-top: 5px; }
  .title-band {
    position: absolute; left: 23px; top: 245px; width: 451px; height: 65px;
    background: var(--orange-band);
    display: flex; align-items: center; justify-content: center;
  }
  .title-band h1 {
    font-family: "Oswald", sans-serif; font-weight: 600;
    font-size: 45px; color: var(--white); letter-spacing: 0.5px; line-height: 1;
  }
  .stats { position: absolute; left: 221px; top: 348px; font-size: 10.5px; }
  .stats div { display: flex; height: 17px; align-items: center; }
  .stats dt { width: 98px; color: var(--orange); font-weight: 700; }
  .stats dd { color: var(--ink); }
  .address-bar {
    position: absolute; left: 197px; top: 403px; width: 277px; height: 17px;
    background: var(--orange); color: var(--white);
    font-size: 7.4px; font-weight: 700;
    display: flex; align-items: center; padding-left: 24px; gap: 7px;
  }
  .address-bar svg { position: absolute; left: 23px; top: 3px; }
  .address-bar span { margin-left: 21px; }
  .features { position: absolute; left: 217px; top: 438px; }
  .features h2 { font-size: 19px; line-height: 1.25; font-weight: 400; color: var(--orange); }
  .features h2 strong { display: block; color: var(--ink); font-weight: 700; }
  .features__rule { width: 150px; height: 2px; background: var(--orange); margin: 6px 0 9px; }
  .bullets { list-style: none; }
  .bullets li {
    position: relative; padding-left: 23px; font-size: 11.8px; line-height: 18.5px; color: var(--ink);
  }
  .bullets li::before {
    content: ""; position: absolute; left: 11px; top: 5px; width: 7px; height: 7px; background: var(--orange);
  }
  .contact-bar {
    position: absolute; left: 0; top: 569px; width: 498px; height: 50px;
    background: var(--grey-bar); text-align: center;
  }
  .contact-bar h3 { color: var(--white); font-size: 12px; font-weight: 700; margin-top: 10px; }
  .contact-row {
    display: flex; justify-content: center; gap: 20px; margin-top: 4px;
    color: var(--orange); font-size: 12.5px; font-weight: 500;
  }
  .contact-row span { display: flex; align-items: center; gap: 6px; }

  /* Back */
  .floorplan { left: 86px; top: 25px; width: 320px; height: 244px; background: linear-gradient(180deg, #f4f4f4, #e6e6e6); }
  .rate-band {
    position: absolute; left: 0; top: 284px; width: 498px; height: 68px;
    background: var(--orange); color: var(--white); padding: 11px 0 0 38px;
  }
  .rate-band h2 { font-size: 14px; font-weight: 600; }
  .rate-band p { font-size: 11px; margin-top: 6px; line-height: 1.6; padding-left: 6px; }
  .details { position: absolute; left: 37px; top: 372px; width: 290px; list-style: none; }
  .details > li {
    position: relative; padding-left: 14px; font-size: 7.9px; line-height: 11.6px;
    color: var(--ink); margin-bottom: 8px;
  }
  .details > li::before {
    content: ""; position: absolute; left: 0; top: 2px; width: 6px; height: 6px; background: var(--orange);
  }
  .suites { list-style: none; margin-top: 8px; }
  .suites li { position: relative; padding-left: 15px; margin-bottom: 7px; }
  .suites li::before {
    content: "›"; position: absolute; left: 6px; top: -1px; color: var(--orange); font-weight: 700;
  }
  .side-photo { left: 347px; width: 117px; }
</style>
</head>
<body>

<section class="page page--front" aria-label="Flyer front">
  <div class="block" style="left:54px;top:0;width:163px;height:23px"></div>
  <div class="block" style="left:374px;top:0;width:124px;height:123px"></div>
  <div class="block" style="left:54px;top:322px;width:32px;height:247px"></div>
  <div class="block" style="left:54px;top:619px;width:88px;height:24px"></div>

  <div class="photo photo--office hero" role="img" aria-label="Furnished executive office with arched window and desk"></div>

  <div class="brand">
    <span class="brand__name">NORVALE</span>
    <span class="brand__sub">COMPANIES</span>
  </div>

  <div class="title-band"><h1>HALE ROAD CENTRE</h1></div>

  <div class="photo photo--window photo--framed" style="left:90px;top:340px;width:103px;height:95px" role="img" aria-label="Office desk beside an arched window"></div>
  <div class="photo photo--room photo--framed" style="left:87px;top:455px;width:103px;height:96px" role="img" aria-label="Private office with desk and framed artwork"></div>

  <dl class="stats">
    <div><dt>BUILDING SIZE</dt><dd>:&nbsp; 18,325 SF</dd></div>
    <div><dt>VACANT SF</dt><dd>:&nbsp; 3,791 SF</dd></div>
    <div><dt>OCCUPANCY</dt><dd>:&nbsp; 79%</dd></div>
  </dl>

  <div class="address-bar">
    <svg width="9" height="12" viewBox="0 0 9 12" aria-hidden="true"><path d="M4.5 0C2 0 0 2 0 4.5 0 7.8 4.5 12 4.5 12S9 7.8 9 4.5C9 2 7 0 4.5 0Zm0 6.3a1.8 1.8 0 1 1 0-3.6 1.8 1.8 0 0 1 0 3.6Z" fill="#fff"/></svg>
    <span>5220 HALE ROAD, CEDAR GROVE, FL 33499</span>
  </div>

  <div class="features">
    <h2>FEATURES &amp;<strong>AMENITIES</strong></h2>
    <div class="features__rule"></div>
    <ul class="bullets">
      <li>Plenty of parking</li>
      <li>On-site management</li>
      <li>Some furniture available if needed.</li>
    </ul>
  </div>

  <div class="contact-bar">
    <h3>FOR LEASING INFORMATION PLEASE CONTACT</h3>
    <div class="contact-row">
      <span><svg width="13" height="13" viewBox="0 0 13 13" aria-hidden="true"><circle cx="6.5" cy="6.5" r="6.5" fill="#d98f2b"/><circle cx="6.5" cy="5" r="2.2" fill="#7a7a7a"/><path d="M2.8 10.5c.8-1.8 2.1-2.6 3.7-2.6s2.9.8 3.7 2.6" fill="#7a7a7a"/></svg>Dana Whitfield</span>
      <span><svg width="13" height="13" viewBox="0 0 13 13" aria-hidden="true"><circle cx="6.5" cy="6.5" r="6.5" fill="#d98f2b"/><path d="M4.2 3.3l1.3 1.6-.7 1c.5 1 1.2 1.7 2.1 2.2l1-.7 1.6 1.3-.7 1.2C6.3 9.7 3.5 7 3 4.1Z" fill="#7a7a7a"/></svg>555-014-2290</span>
      <span><svg width="13" height="13" viewBox="0 0 13 13" aria-hidden="true"><circle cx="6.5" cy="6.5" r="6.5" fill="#d98f2b"/><rect x="3.3" y="4.3" width="6.4" height="4.4" fill="#7a7a7a"/><path d="M3.3 4.3l3.2 2.4 3.2-2.4" stroke="#d98f2b" stroke-width=".8" fill="none"/></svg>dana@norvalecompanies.com</span>
    </div>
  </div>
</section>

<section class="page page--back" aria-label="Flyer back">
  <div class="block" style="left:0;top:0;width:498px;height:18px"></div>

  <div class="photo floorplan" role="img" aria-label="Floor plan showing Suite 100 and Suite 120"></div>

  <div class="rate-band">
    <h2>Rental Rate: $32.00/SF plus suite electric</h2>
    <p>- No extra operating expenses.<br>- Very easy to show as landlord is in the building.</p>
  </div>

  <div class="block" style="left:367px;top:352px;width:78px;height:14px"></div>
  <div class="photo photo--room side-photo" style="top:371px;height:107px" role="img" aria-label="Office with round meeting table and whiteboard"></div>
  <div class="block" style="left:367px;top:484px;width:78px;height:11px"></div>
  <div class="photo photo--window side-photo" style="top:499px;height:109px" role="img" aria-label="Conference room with long table and arched window"></div>
  <div class="block" style="left:367px;top:613px;width:78px;height:10px"></div>
  <div class="block" style="left:0;top:623px;width:498px;height:20px"></div>

  <ul class="details">
    <li>The Hale Road Centre is a beautiful Class A building situation in the heart of Cedar Grove but without the crazy Parkway traffic.</li>
    <li>Hale Road Centre is located directly on I-95 just off of Hale Road. The massive, new Marlowe development south entrance is being built across the street. The building is very convenient to restaurants, shopping, and every other trade needed.</li>
    <li>The suites are incredibly well appointed and move-in ready with custom oak doors and millwork, 10' ceilings, floor to ceiling windows</li>
    <li>Two suites are available, which can be combined for 3,791 SF in total.
      <ul class="suites">
        <li>Suite 120 is available right now and is 1,488 SF with 1 large executive office, 2 smaller offices, a conference room, break room, and reception area.</li>
        <li>Suite 100 is available in February 2019, but could be vacated sooner. Suite 120 is 2,303 SF and has 6 offices, break room, reception area, and a very large meeting room.</li>
      </ul>
    </li>
  </ul>
</section>

</body>
</html>
```